Plant based protein powders and bars in different flavors need a packaging design

I need a packaging design for a new company called "Vale Verdura". We develop plant based protein powders and Bars which are made with completely organic food ingredients and are completely free of preservative and artificial additives. The aim is to create something that speaks purity, Doesn't mislead the customer and signifies Pure and natural food. Sun gives life to vegetation and that's what we use to survive. We will use both stand-up pouches and tubs to sell our powder. So I need a packaging design for both.The protein bars are something where I would like to try and be creative with the packaging. There are multiple flavors. For each flavor we need a different color theme but the overall theme should remain the same.

Target Market(s)

working individuals who are looking for too busy to eat a complete nutritious meal or lack time to make one. Target consumer needs something that they can consume anytime they want, irrespective of the place they're at. Nutrition deprived people are our target consumers.

Industry/Entity Type

Nutrition

Font styles to use
Serif
Decorative

Colors

Designer to choose colors to be used in the design.

Requirements
Must have
• Unique Eye catching packaging design. Simple yet elegant. Something that says Pure and Simple yet powerful and effective.
Should not have
• Complex packaging that makes it harder for consumers to make a buying decision.

```html
<!DOCTYPE html>
<html lang="en">
<head>
<meta charset="utf-8">
<title>Vale Verdura – Protein Tub Labels</title>
<link href="https://fonts.googleapis.com/css2?family=Montserrat:wght@800&family=Open+Sans:wght@400;600;700&family=Cormorant+Garamond:wght@500&display=swap" rel="stylesheet">
<style>
  :root{
    --canvas:#d9d9d9;
    --label-bg:#f7f8f8;
    --label-bg-edge:#eceef0;
    --ink:#3a3a3a;
    --protein-light:#8fcf7e;
    --protein-dark:#137a2a;
    --stat-green:#3daa4a;
    --orange-1:#f6b24c;
    --orange-2:#e07a26;
    --orange-3:#c2531a;
    --mint-1:#bfe28f;
    --mint-2:#8a9a55;
    --choc-1:#6b3a1e;
    --choc-2:#4a2414;
    --badge-blue:#8aa9d8;
    --badge-green:#5cae6b;
    --badge-orange:#e69a33;
  }
  *{box-sizing:border-box;margin:0;padding:0}
  html,body{width:1200px;height:918px;overflow:hidden}
  body{background:linear-gradient(180deg,#cfcfcf,#e6e6e6);font-family:"Open Sans",sans-serif;position:relative}

  .label{position:absolute;top:179px;width:440px;height:560px;overflow:hidden;
    background:radial-gradient(ellipse at 50% 45%,var(--label-bg) 40%,var(--label-bg-edge) 100%);
    box-shadow:0 6px 18px rgba(0,0,0,.12)}
  .label--orange{left:100px;--t1:var(--orange-1);--t2:var(--orange-2);--t3:var(--orange-3)}
  .label--mint{left:660px;--t1:var(--mint-1);--t2:var(--mint-2);--t3:var(--choc-2)}

  .top-wave{position:absolute;left:0;top:0;width:440px;height:110px}

  .brand-name{position:absolute;left:0;width:100%;top:92px;text-align:center;padding-left:30px;
    font-family:"Cormorant Garamond",serif;font-weight:500;font-size:24px;letter-spacing:1.5px;color:var(--ink);white-space:nowrap}

  .product-name{position:absolute;left:56px;top:158px;font-family:"Montserrat",sans-serif;font-weight:800;font-size:76px;letter-spacing:-4px;line-height:1;
    background:linear-gradient(90deg,var(--protein-light),var(--protein-dark));-webkit-background-clip:text;background-clip:text;color:transparent}
  .product-sub{position:absolute;right:52px;top:241px;font-size:11px;letter-spacing:3.2px;color:var(--ink);font-weight:600}

  .flavor{position:absolute;left:76px;top:276px;width:294px;height:35px;
    background:linear-gradient(90deg,var(--t1),var(--t2) 55%,var(--t3));
    color:#fff;font-weight:700;font-size:26px;letter-spacing:1px;text-align:center;line-height:35px}

  .claims{position:absolute;left:0;width:100%;top:320px;display:flex;justify-content:center;gap:12px;font-size:7.5px;font-weight:700;color:#555;letter-spacing:.5px}
  .claim{display:flex;align-items:center;gap:5px}
  .claim__dot{width:14px;height:14px;border-radius:50%}
  .claim__dot--blue{background:var(--badge-blue)}
  .claim__dot--green{background:var(--badge-green)}
  .claim__dot--orange{background:var(--badge-orange)}

  .stats{position:absolute;left:172px;top:354px;width:102px;height:25px;background:var(--stat-green);color:#fff;display:flex}
  .stat{flex:1;text-align:center;line-height:1}
  .stat + .stat{border-left:1px solid rgba(255,255,255,.8)}
  .stat__value{display:block;font-size:16px;margin-top:2px}
  .stat__unit{display:block;font-size:5px;letter-spacing:1px}

  .seal{position:absolute;left:76px;top:414px;width:54px;height:54px;border-radius:50%;border:2px solid var(--t2);
    display:flex;align-items:center;justify-content:center;text-align:center;font-size:6px;line-height:1.35;color:var(--t2)}

  .flavor-art{position:absolute;left:130px;top:405px;width:190px;height:100px;border-radius:40px 40px 30px 30px}
  .label--orange .flavor-art{background:radial-gradient(ellipse at 50% 50%,#f7a330,#e07a10 70%,rgba(224,122,16,0) 100%)}
  .label--mint .flavor-art{background:radial-gradient(ellipse at 50% 55%,#8a5530,#5d8f4a 65%,rgba(93,143,74,0) 100%)}

  .net-weight{position:absolute;left:0;width:100%;top:518px;text-align:center;font-size:10px;font-weight:700;color:var(--ink);padding-left:10px}
  .bottom-band{position:absolute;left:0;bottom:0;width:100%;height:26px;background:linear-gradient(90deg,var(--t1),var(--t2) 55%,var(--t3))}
</style>
</head>
<body>

<section class="label label--orange">
  <svg class="top-wave" viewBox="0 0 440 110" aria-hidden="true">
    <defs>
      <linearGradient id="waveOrange" x1="0" x2="1"><stop offset="0" stop-color="var(--orange-1)"/><stop offset=".55" stop-color="var(--orange-2)"/><stop offset="1" stop-color="var(--orange-3)"/></linearGradient>
    </defs>
    <path d="M0 0H440V28C390 30 340 66 270 66C205 66 160 30 100 34C55 37 25 58 0 72Z" fill="url(#waveOrange)" opacity=".45"/>
    <path d="M0 0H440V18C395 22 345 52 275 52C210 52 165 18 105 22C60 25 25 42 0 52Z" fill="url(#waveOrange)"/>
  </svg>
  <div class="brand-name">Vale Verdura</div>
  <div class="product-name">PROTEIN</div>
  <div class="product-sub">COMPLETE PLANT BASED</div>
  <div class="flavor">MINT CHOCOLATE</div>
  <div class="claims">
    <span class="claim"><span class="claim__dot claim__dot--blue"></span>GLUTEN FREE</span>
    <span class="claim"><span class="claim__dot claim__dot--green"></span>DAIRY FREE</span>
    <span class="claim"><span class="claim__dot claim__dot--orange"></span>NON-GMO</span>
  </div>
  <div class="stats">
    <div class="stat"><span class="stat__value">20G</span><span class="stat__unit">PROTEIN</span></div>
    <div class="stat"><span class="stat__value">170</span><span class="stat__unit">CALORIES</span></div>
  </div>
  <div class="seal">Free of<br>Artificial<br>Additives</div>
  <div class="flavor-art" role="img" aria-label="Photo of whole and sliced oranges"></div>
  <div class="net-weight">NET WT. 2LB</div>
  <div class="bottom-band"></div>
</section>

<section class="label label--mint">
  <svg class="top-wave" viewBox="0 0 440 110" aria-hidden="true">
    <defs>
      <linearGradient id="waveMint" x1="0" x2="1"><stop offset="0" stop-color="var(--mint-1)"/><stop offset=".5" stop-color="var(--mint-2)"/><stop offset="1" stop-color="var(--choc-1)"/></linearGradient>
    </defs>
    <path d="M0 0H440V28C390 30 340 66 270 66C205 66 160 30 100 34C55 37 25 58 0 72Z" fill="url(#waveMint)" opacity=".45"/>
    <path d="M0 0H440V18C395 22 345 52 275 52C210 52 165 18 105 22C60 25 25 42 0 52Z" fill="url(#waveMint)"/>
  </svg>
  <div class="brand-name">Vale Verdura</div>
  <div class="product-name">PROTEIN</div>
  <div class="product-sub">COMPLETE PLANT BASED</div>
  <div class="flavor">MINT CHOCOLATE</div>
  <div class="claims">
    <span class="claim"><span class="claim__dot claim__dot--blue"></span>GLUTEN FREE</span>
    <span class="claim"><span class="claim__dot claim__dot--green"></span>DAIRY FREE</span>
    <span class="claim"><span class="claim__dot claim__dot--orange"></span>NON-GMO</span>
  </div>
  <div class="stats">
    <div class="stat"><span class="stat__value">20G</span><span class="stat__unit">PROTEIN</span></div>
    <div class="stat"><span class="stat__value">170</span><span class="stat__unit">CALORIES</span></div>
  </div>
  <div class="seal">Free of<br>Artificial<br>Additives</div>
  <div class="flavor-art" role="img" aria-label="Photo of mint chocolates with fresh mint leaves"></div>
  <div class="net-weight">NET WT. 2LB</div>
  <div class="bottom-band"></div>
</section>

</body>
</html>
```